To design a brand identity that is simple and creative with 'Corvane' as the brand name, I like modern simple fonts like helvetica neue, I want to print both sides of the card, I am open to dark front and white back, but the design needs to transfer well to letter heads and email signatures, I am looking for sophisticated and elegant, but open minded about clever and off the wall, I do not do 'boring' Corvane Ventures is the mother company for a small group, specialising in Management & consulting, Software development and construction, we have a high level of integrity, we are transparent and accountable for what we do. my images are provided as a guide only, Im not expecting them to be just copied, Im looking for a creator and passionate thinker, who will put life into their work.

Target Market(s)

usually business minded people who are looking for something different in me, such as leadership, confidence and focus with thinking that is per haps a little outside the box..

Industry/Entity Type

Construction

Requirements
Must have
• clean, minmalistic
Nice to have
• custom logo
Should not have
• boring, traditional

```html
<!DOCTYPE html>
<html lang="en">
<head>
<meta charset="utf-8">
<title>Corvane — Business Card, Front and Back</title>
<link rel="stylesheet" href="https://fonts.googleapis.com/css2?family=Inter:wght@200;300;400;500&display=swap">
<style>
  :root {
    --stage: #2f2b29;
    --label: #d9d6d3;
    --card-light: #e6e7e8;
    --card-light-edge: #d2d3d5;
    --card-dark: #2a2a2a;
    --card-dark-glow: #4a4645;
    --ink: #1d1d1d;
    --ink-soft: #3a3a3a;
    --ghost: rgba(150, 150, 150, 0.45);
    --accent: #e0311f;
    --accent-soft: #e0654f;
    --paper-white: #ffffff;
    --tag-grey: #d8d8d8;
  }
  * { margin: 0; padding: 0; box-sizing: border-box; }
  html, body { width: 1000px; height: 1200px; overflow: hidden; }
  body {
    background: var(--stage);
    font-family: "Inter", "Helvetica Neue", Arial, sans-serif;
    position: relative;
  }
  .set-label, .side-label {
    position: absolute;
    color: var(--label);
    font-size: 20px;
    font-weight: 400;
  }
  .set-label { left: 32px; top: 30px; }
  .side-label--front { left: 811px; top: 570px; color: var(--paper-white); }
  .side-label--back { left: 117px; top: 1144px; }

  .card {
    position: absolute;
    width: 740px;
    height: 456px;
    overflow: hidden;
  }
  /* Front */
  .card--front { left: 136px; top: 75px; }
  .card__texture {
    position: absolute; inset: 0;
    background: linear-gradient(135deg, var(--card-light) 0%, #f1f1f2 40%, var(--card-light-edge) 100%);
  }
  .brand-mark {
    position: absolute;
    display: flex;
    align-items: center;
  }
  .brand-mark--front { left: 46px; top: 206px; gap: 14px; }
  .brand-mark__dot {
    width: 44px; height: 44px; border-radius: 50%;
    background: var(--accent-soft);
  }
  .brand-mark__name {
    font-weight: 300;
    line-height: 1;
  }
  .brand-mark--front .brand-mark__name { font-size: 52px; color: var(--ink); }

  .divisions-vertical {
    position: absolute;
    left: 354px; top: 55px; height: 345px; width: 30px;
    writing-mode: vertical-rl;
    transform: rotate(180deg);
    font-size: 15px;
    letter-spacing: 0.6px;
    color: var(--ink);
    text-align: center;
    white-space: nowrap;
  }
  .sep { color: var(--accent); padding: 3px 0; }
  .ghost-name {
    position: absolute;
    left: 326px; top: 110px; height: 260px; width: 70px;
    writing-mode: vertical-rl;
    transform: rotate(180deg);
    font-size: 70px;
    font-weight: 200;
    color: var(--ghost);
    line-height: 1;
    white-space: nowrap;
  }
  .contact {
    position: absolute;
    left: 453px; top: 136px;
    color: var(--ink);
  }
  .contact__name { font-size: 25px; font-weight: 400; line-height: 1.2; }
  .contact__role { font-size: 15px; font-weight: 400; margin-bottom: 10px; }
  .contact__list { list-style: none; font-size: 18px; font-weight: 300; line-height: 28px; color: var(--ink-soft); }
  .contact__list li.gap { margin-top: 12px; }
  .contact__key { color: var(--accent-soft); margin-right: 4px; }

  /* Back */
  .card--back {
    left: 117px; top: 652px;
    background: radial-gradient(ellipse 70% 75% at 50% 35%, var(--card-dark-glow) 0%, var(--card-dark) 75%);
  }
  .brand-mark--back { left: 128px; top: 176px; gap: 22px; }
  .brand-mark--back .brand-mark__dot {
    width: 92px; height: 92px;
    background: var(--accent);
  }
  .brand-mark--back .brand-mark__name {
    font-size: 96px; font-weight: 200; color: var(--paper-white);
  }
  .divisions-line {
    position: absolute;
    left: 0; right: 0; top: 296px;
    text-align: center;
    font-size: 15px;
    letter-spacing: 1.5px;
    color: var(--tag-grey);
    font-weight: 400;
  }
  .divisions-line .sep { padding: 0 6px; }
</style>
</head>
<body>
  <div class="set-label">Set 13</div>

  <section class="card card--front" aria-label="Business card front">
    <div class="card__texture" role="img" aria-label="Soft light grey faceted polygon texture"></div>

    <div class="brand-mark brand-mark--front">
      <span class="brand-mark__dot"></span>
      <span class="brand-mark__name">corvane</span>
    </div>

    <div class="ghost-name" aria-hidden="true">corvane</div>
    <div class="divisions-vertical">management <span class="sep">•</span> software <span class="sep">•</span> construction</div>

    <div class="contact">
      <div class="contact__name">Maren Holt</div>
      <div class="contact__role">client ambassador</div>
      <ul class="contact__list">
        <li><span class="contact__key">c.</span>+61 0400 512 947</li>
        <li><span class="contact__key">e.</span>info@corvane.com.au</li>
        <li class="gap"><span class="contact__key">a.</span>po box 318 perth 6011</li>
        <li><span class="contact__key">w.</span>www.corvane.ventures</li>
      </ul>
    </div>
  </section>
  <div class="side-label side-label--front">Front</div>

  <section class="card card--back" aria-label="Business card back">
    <div class="brand-mark brand-mark--back">
      <span class="brand-mark__dot"></span>
      <span class="brand-mark__name">corvane</span>
    </div>
    <div class="divisions-line">management <span class="sep">•</span> software <span class="sep">•</span> construction</div>
  </section>
  <div class="side-label side-label--back">Back</div>
</body>
</html>
```